Design and Renovation Company Luxury Business Card

I want to create a luxury business card for a Design and Renovation Firm . We will use our current logo. The company name is 528BUILDA. We do not want anything standard. We need a very unique concept.
Please see uploaded inspiration. I really like the textured paper option. I would like the card to be thick with debossing, and/or embossing options. The logo has orange in it but I would like to see the card with and without the orange. I think the orange may make the company feel less high-end. The goal is to elevate the logo not match its vibe per se of the logo. We want something very unique, not standard at all!
I would like a space for :
Logo,
Name,
Position,
Email,
Office number,
Website Address,
Business Address,
Thank you!
Have fun!
Target Market(s)
Home owners Age 35 +
Industry/Entity Type
Design and Renovation
Contact Information for Business Card
Logo, Name, Position, Email, Office number, Website Address, Business Address,.
Colors
Designer to choose colors to be used in the design.
Requirements
Must have
- A luxury designer feel. Must be black or dark grey but open to other luxury ideas.
Nice to have
- Gold, silver, black embossing or debossing. Textured paper design.
Should not have
- A cheap look and feel.

```html
<!DOCTYPE html>
<html lang="en">
<head>
<meta charset="utf-8">
<title>528BUILDA Business Card</title>
<link href="https://fonts.googleapis.com/css2?family=Montserrat:wght@400;500;600&display=swap" rel="stylesheet">
<style>
  :root {
    --page-bg: #3a332c;
    --card-bg: #1c1c1c;
    --card-back-bg: #1a1a1a;
    --white: #ffffff;
    --text-soft: #f2f2f2;
    --orange: #f7941d;
    --deboss: #0c0c0c;
    --panel-light: #7a7a7a;
    --panel-dark: #2a2a2a;
  }
  * { margin: 0; padding: 0; box-sizing: border-box; }
  html, body { width: 900px; height: 1200px; overflow: hidden; }
  body {
    position: relative;
    background: var(--page-bg);
    font-family: "Montserrat", sans-serif;
    color: var(--text-soft);
  }
  .card {
    position: absolute;
    border-radius: 28px;
    box-shadow: 0 10px 28px rgba(0,0,0,0.55);
  }
  .card-front { left: 80px; top: 131px; width: 742px; height: 441px; background: var(--card-bg); }
  .card-back  {
    left: 77px; top: 638px; width: 745px; height: 440px;
    background: var(--card-back-bg);
    display: flex; align-items: center; justify-content: center;
  }

  .brand-name {
    white-space: nowrap;
    font-weight: 500;
    line-height: 1;
  }
  .card-front .brand-name {
    position: absolute; left: 42px; top: 60px;
    font-size: 38px; letter-spacing: 2px; color: var(--white);
  }
  .card-back .brand-name {
    font-size: 64px; letter-spacing: 4px; color: var(--deboss);
    text-shadow: 0 1px 0 rgba(255,255,255,0.06);
  }

  .person-name {
    position: absolute; left: 35px; top: 166px;
    font-size: 26px; font-weight: 600; color: var(--orange);
  }
  .person-role { position: absolute; left: 35px; top: 202px; font-size: 16px; font-weight: 400; }
  .address { position: absolute; left: 35px; top: 271px; font-size: 16px; line-height: 21px; }
  .contact-list { position: absolute; left: 34px; top: 331px; list-style: none; }
  .contact-list li {
    display: flex; align-items: center; gap: 9px;
    height: 28.5px; font-size: 16px;
  }
  .contact-list svg { width: 16px; height: 16px; flex: none; }

  .gloss-panel {
    position: absolute; left: 540px; top: 101px; width: 145px; height: 140px;
    border-radius: 3px;
    background: linear-gradient(160deg, var(--panel-light), var(--panel-dark));
    box-shadow: 0 0 10px rgba(0,0,0,0.6);
  }
</style>
</head>
<body>
  <section class="card card-front">
    <p class="brand-name">528BUILDA</p>

    <h1 class="person-name">Daniel Hart</h1>
    <p class="person-role">Managing Director</p>

    <p class="address">415 Maple Grove Ave, #112<br>Fairview, OH 430061</p>

    <ul class="contact-list">
      <li>
        <svg viewBox="0 0 16 16" aria-hidden="true"><path fill="#f7941d" d="M3.6 1.5l2.3 2.6-1.3 1.6c.9 2 2.6 3.7 4.7 4.7l1.6-1.3 2.6 2.3-1.2 2.1C7.4 13.3 2.7 8.6 1.5 3.7z"/></svg>
        555-318-0427
      </li>
      <li>
        <svg viewBox="0 0 16 16" aria-hidden="true"><rect x="2" y="4" width="12" height="8.5" fill="#f7941d"/><path d="M2 4.5l6 4.2 6-4.2" fill="none" stroke="#1c1c1c" stroke-width="1.2"/></svg>
        info@528builda.com
      </li>
      <li>
        <svg viewBox="0 0 16 16" aria-hidden="true"><circle cx="8" cy="8" r="6.5" fill="#f7941d"/><path d="M1.5 8h13M8 1.5c-2.4 2.5-2.4 10.5 0 13M8 1.5c2.4 2.5 2.4 10.5 0 13" fill="none" stroke="#1c1c1c" stroke-width="1"/></svg>
        www.528builda.com
      </li>
    </ul>

    <div class="gloss-panel" role="img" aria-label="Glossy spot-varnish square panel"></div>
  </section>

  <section class="card card-back">
    <p class="brand-name">528BUILDA</p>
  </section>
</body>
</html>
```